Modern, traditional Catering Menu for hotel and conference centre

Modernization of Catering menu while still making this very legible and clear to all guests. Template required in Microsoft word document so that updates to menu items can be easily updated. Menu needs style relatable to hotel and conference centre in an area known for apples, farming and awe-inspiring landscape.

Target Market(s)

Conference and meeting groups,

Industry/Entity Type

Hospitality

Font styles to use
Serif
Script

Colors

Designer to choose colors to be used in the design.

Requirements
Must have
• Legible and clear headers and modern look.
• Microsoft word template to easily be able to make updates.
Nice to have
• Something unique related to apples and our logo

```html
<!DOCTYPE html>
<html lang="en">
<head>
<meta charset="utf-8">
<title>Harvest Hill Inn – Catering Menu</title>
<link rel="stylesheet" href="https://fonts.googleapis.com/css2?family=Crimson+Text:ital,wght@0,400;0,600;0,700;1,400;1,600&family=Libre+Baskerville:wght@700&display=swap">
<style>
:root{
  --ink:#1f1c12;
  --title:#7d7a6c;
  --muted:#807c6a;
  --rule:#8a7a55;
  --leaf-top:#f2efdc;
  --leaf-mid:#c9d67a;
  --grass:#9fc24a;
  --warm:#e4cf8a;
}
*{margin:0;padding:0;box-sizing:border-box}
html,body{width:1200px;height:847px;overflow:hidden;background:#fff}
.spread{position:relative;width:1200px;height:847px;font-family:"Crimson Text",Georgia,serif;color:var(--ink);font-size:13px;line-height:14.1px}
.backdrop{position:absolute;inset:0;
  background:
   radial-gradient(ellipse 420px 300px at 300px 520px,rgba(150,200,60,.55),transparent 70%),
   radial-gradient(ellipse 500px 400px at 900px 250px,rgba(232,205,130,.55),transparent 70%),
   linear-gradient(180deg,var(--leaf-top) 0%,#e6e7b6 30%,var(--leaf-mid) 60%,var(--warm) 100%);}
.page{position:absolute;top:0;width:600px;height:847px}
.page--left{left:0}.page--right{left:600px}
.masthead{position:absolute;top:28px;left:0;right:0;text-align:center}
.masthead__name{font-family:"Libre Baskerville",Georgia,serif;font-weight:700;font-size:18px;color:var(--title);display:inline-flex;align-items:center;gap:8px}
.masthead__mark{width:16px;height:16px;border-radius:50%;background:var(--title);display:inline-block}
.masthead__sub{font-style:italic;font-weight:600;font-size:10px;color:var(--muted);margin-top:6px}
.block{position:absolute}
.page--left .block{left:30px;width:535px}
.page--right .block{left:30px;width:540px}
.section-title{font-size:19px;line-height:20px;display:flex;justify-content:space-between;align-items:flex-end}
.section-title small{font-size:13px}
.section-title--lg{font-size:25px;line-height:26px}
.section-title--lg small{font-size:13px;margin-left:4px}
.row{display:flex;justify-content:space-between}
.row--head{font-size:16px;line-height:17px}
.item{margin-bottom:19px}
.item-name{font-size:16px;line-height:17px;display:flex;justify-content:space-between}
.note{font-size:13px}
.rule{position:absolute;left:30px;right:30px;top:786px;height:1px;background:var(--rule)}
.page-no{position:absolute;right:30px;top:794px;font-size:10px;color:var(--muted)}
.footer{position:absolute;left:0;right:0;top:808px;text-align:center;font-size:8.5px;line-height:11px;color:var(--muted)}
</style>
</head>
<body>
<div class="spread">
  <div class="backdrop" role="img" aria-label="Photograph of apple tree branches with ripe red apples over a green orchard lawn"></div>

  <section class="page page--left">
    <header class="masthead">
      <div class="masthead__name">Harvest Hill Inn Hotel &amp; Conference Centre <span class="masthead__mark"></span></div>
      <div class="masthead__sub">Conference Groups Cider Hall</div>
    </header>

    <div class="block" style="top:82px">
      <div class="section-title">Meeting Refreshments</div>
      <div class="row"><span>From the Bakery</span><span>Per Piece</span></div>
      <div class="row"><span>Assorted Muffins</span><span>2.00</span></div>
      <div class="row"><span>Selection of Fresh Baked Cookies</span><span>2.00</span></div>
      <div class="row"><span>Bagels with cream cheese</span><span>2.00</span></div>
      <div class="row"><span>Cinnamon swirls</span><span>2.00</span></div>
      <div class="row"><span>Danish (minis, assortment)</span><span>1.75</span></div>
      <div class="row"><span>Oatcakes half dipped in chocolate</span><span>2.25</span></div>
      <div class="row"><span>Scones (minis, assortment)</span><span>1.75</span></div>
      <div class="row"><span>Gluten Free Muffins (min of six (6) ordered per day - advance notice)</span><span>3.00</span></div>
      <div class="row"><span>Sliced Banana Bread and/or Lemon Loaf</span><span>21.95/loaf</span></div>
    </div>

    <div class="block" style="top:248px">
      <div class="section-title">Heart Smart <small>Per Person</small></div>
      <div class="row"><span>Whole Fresh Fruit (apples, oranges &amp; bananas)</span><span>2.75</span></div>
      <div class="row"><span>Crisp Vegetables with dip</span><span>5.25</span></div>
      <div class="row"><span>Rainbow of Sliced Fresh Fruit with yogurt dip</span><span>5.25</span></div>
      <div class="row"><span>Fresh Fruit Skewers with yogurt or chocolate dip</span><span>5.25</span></div>
      <div class="row"><span>Domestic and Imported Cheese Platter with fruit garnish</span><span>6.95</span></div>
      <div class="row"><span>Low Fat Individual Yogurt (assorted flavours)</span><span>2.60</span></div>
      <div class="row"><span>Low Fat Yogurt &amp; Granola Parfait (presented in individual glasses)</span><span>4.25</span></div>
      <div class="row"><span>Fruit Cup (gluten free option)</span><span>4.75</span></div>
    </div>

    <div class="block" style="top:394px">
      <div class="section-title">Beverages <small>Per Serving</small></div>
      <div class="row"><span>Freshly Brewed Coffee, Decaffeinated Coffee or Tea</span><span>2.75</span></div>
      <div class="row"><span>Herbal Tea (assorted flavours)</span><span>2.95</span></div>
      <div class="row"><span>Assorted Soft Drinks (cans)</span><span>2.50</span></div>
      <div class="row"><span>Hot Chocolate</span><span>2.50</span></div>
      <div class="row"><span>Bottled Spring Water</span><span>2.75</span></div>
      <div class="row"><span>Assorted Chilled Juices (individual bottles)</span><span>2.75</span></div>
      <div class="row"><span>Sparkling Mineral Water</span><span>3.00</span></div>
      <div class="row" style="margin-top:14px"><span>Pot of Freshly Brewed Coffee (10 cups)</span><span>27.50/pot</span></div>
      <div class="row"><span>Carafe of Freshly Brewed Coffee (15 cups)</span><span>41.25/carafe</span></div>
    </div>

    <div class="block" style="top:568px">
      <div class="section-title">Packages <small style="margin-right:auto;margin-left:4px">(Minimum of 10 people)</small><small>Per Person</small></div>
      <div class="row row--head"><span>Morning Kick Start</span><span style="font-size:13px">6.35</span></div>
      <div class="row"><span>Freshly Brewed Coffee, Tea, Juice, Muffins &amp; Oatcakes half dipped in chocolate</span></div>
      <div class="row row--head"><span>Afternoon Energizer</span><span style="font-size:13px">6.30</span></div>
      <div class="row"><span>Freshly Brewed Coffee, Tea, Soft Drinks &amp; Cookies</span></div>
      <div class="row row--head" style="margin-top:14px"><span>Bakery Basket</span><span style="font-size:13px">4.50</span></div>
      <div class="row"><span>An assortment of Pastries, Muffins, Scones &amp; Whole Fruit</span></div>
      <div class="row row--head" style="margin-top:14px"><span>Sweet Treat</span><span style="font-size:13px">5.65</span></div>
      <div class="row"><span>An assortment of Cookies, Squares &amp; Fruit Skewers</span></div>
    </div>

    <p class="block" style="top:748px">Allergy notification: baked food items may contain trace amounts of wheat, tree nuts and peanuts. Please ask if you have any allergies, questions or concerns.</p>

    <div class="rule"></div>
    <div class="page-no">Page 3</div>
    <footer class="footer">
      Exit 4, Valley Highway, 28 Orchard Lane, Maplebrook, Valley County, A1B 2C3<br>
      T: (555) 010 2040 &nbsp; TF: 1 800 555 0199 &nbsp; F: (555) 010 2041<br>
      Effective: January 1, 2019. All prices are plus 16% gratuity plus applicable taxes and are subject to change
    </footer>
  </section>

  <section class="page page--right">
    <header class="masthead">
      <div class="masthead__name">Harvest Hill Inn Hotel &amp; Conference Centre <span class="masthead__mark"></span></div>
      <div class="masthead__sub">Conference Groups Cider Hall</div>
    </header>

    <div class="block" style="top:106px">
      <div class="section-title section-title--lg" style="justify-content:flex-start">Breakfast Selections <small>Available until 10:00am</small></div>
      <p>Minimum of twenty (20) guests</p>
      <p>A surcharge of $1.95 per person will apply to groups under 20 guests</p>
    </div>

    <div class="block" style="top:174px">
      <div class="section-title section-title--lg" style="margin-bottom:10px">Plated Service</div>
      <div class="item">
        <div class="item-name"><span>The Orchard</span><span style="font-size:13px">13.95</span></div>
        <p>Fresh melon wedges, apple pancakes with syrup, honey baked ham, muffins &amp; assorted jams, chilled juice (apple or orange), with freshly brewed coffee or tea</p>
      </div>
      <div class="item">
        <div class="item-name"><span>Valley Express</span><span style="font-size:13px">14.95</span></div>
        <p>Scrambled eggs, home fried potatoes, crisp bacon slices, muffins &amp; assorted jams, chilled juice (apple or orange), with freshly brewed coffee or tea</p>
      </div>
      <div class="item">
        <div class="item-name"><span>Breakfast Wrap</span><span style="font-size:13px">14.95</span></div>
        <p>Scrambled eggs with sautéed peppers &amp; onions garnished with shredded cheese wrapped in a flour tortilla shell served with home fried potatoes &amp; apple wedges, chilled juice (apple or orange), with freshly brewed coffee or tea</p>
      </div>
    </div>

    <div class="block" style="top:410px">
      <div class="section-title section-title--lg">Buffet Service</div>
      <p>Minimum of thirty (30) guests</p>
      <p>A surcharge of $1.95 per person will apply to groups under 30 guests</p>
    </div>

    <div class="block" style="top:490px">
      <div class="item">
        <div class="item-name"><span>Meadowlark Continental Buffet (cold)</span><span style="font-size:13px">10.95</span></div>
        <p>Selection of cereals, breakfast pastries, muffins, butter &amp; assorted jams, apples, chilled juice (apple &amp; orange), with freshly brewed coffee or tea</p>
      </div>
      <div class="item">
        <div class="item-name"><span>Healthy Quick Start Buffet (hot)</span><span style="font-size:13px">13.95</span></div>
        <p>Scrambled eggs, yogurt, granola, apples, chilled juice (apple &amp; orange), toast, English muffins and assorted jams, with freshly brewed coffee or tea</p>
      </div>
      <div class="item">
        <div class="item-name"><span>Ridgeview Buffet (hot)</span><span style="font-size:13px">16.95</span></div>
        <p>Scrambled eggs, bacon or sausages, home fried potatoes, apple pancakes or French toast, selection of cereals, fresh fruit &amp; yogurt, chilled juice (apple or orange), with freshly brewed coffee or tea</p>
      </div>
    </div>

    <p class="block" style="top:714px">Gluten free bread is available upon request with an additional charge of $2.00 per person</p>

    <div class="rule"></div>
    <div class="page-no">Page 4</div>
    <footer class="footer">
      Exit 4, Valley Highway, 28 Orchard Lane, Maplebrook, Valley County, A1B 2C3<br>
      T: (555) 010 2040 &nbsp; TF: 1 800 555 0199 &nbsp; F: (555) 010 2041<br>
      Effective: January 1, 2019. All prices are plus 16% gratuity plus applicable taxes and are subject to change
    </footer>
  </section>
</div>
</body>
</html>
```